Coffeeshop menu for filter tip

We want to have a cannabis (coffeeshop) menu in the size 25mm wide x 60mm wide. Some examples attached.

it must have the following text:
Menu

WEED p/g
Oblivane €16
Cloudplum €14
Tide Runner €14
Quincefig €16
Mega Marsh €14
Grey Heron €14

HASH p/g
Tashar Amber €12
Pebble Frost€11
Lime Dunes €14
Ash Petal €10

Target Market(s)

tourist in Amsterdam

Requirements
Nice to have
• cannabis sign leaf
• No Cigarettes allowed symbol

```html
<!DOCTYPE html>
<html lang="en">
<head>
<meta charset="utf-8">
<title>Amsterdam Menu</title>
<link rel="stylesheet" href="https://fonts.googleapis.com/css2?family=Kaushan+Script&family=Oswald:wght@700&family=Ubuntu:wght@400&display=swap">
<style>
  :root {
    --bg-dark: #1f0c08;
    --bg-brown: #6b3515;
    --bg-copper: #9a5420;
    --bg-wine: #3d0f0d;
    --cream: #ece6cc;
    --white: #ffffff;
    --yellow: #f8ee74;
    --ring-brown: #6a3a1c;
    --leaf-green: #5cb030;
    --no-red: #e0262b;
  }
  * { margin: 0; padding: 0; box-sizing: border-box; }
  html, body { width: 1200px; height: 2878px; overflow: hidden; background: var(--bg-dark); }
  .menu-card { position: relative; width: 1200px; height: 2878px; overflow: hidden; }
  .backdrop {
    position: absolute; inset: 0;
    background:
      linear-gradient(160deg, rgba(190,150,120,0.0) 60%, rgba(190,160,130,0) 100%),
      radial-gradient(ellipse at 70% 18%, var(--bg-copper) 0%, transparent 55%),
      radial-gradient(ellipse at 25% 75%, #6e2a14 0%, transparent 50%),
      linear-gradient(180deg, var(--bg-brown) 0%, #4a2010 35%, var(--bg-wine) 60%, #2a0c0a 85%, #140706 100%);
  }
  .frame { position: absolute; inset: 0; }
  .emblem {
    position: absolute; left: 410px; top: 109px; width: 378px; height: 378px;
    border-radius: 50%; background: var(--white);
    box-shadow: 0 0 0 12px var(--ring-brown), 0 0 0 20px var(--white);
  }
  .emblem-fill {
    position: absolute; left: 50%; top: 50%; width: 270px; height: 270px;
    transform: translate(-50%, -50%); border-radius: 50%;
    background: radial-gradient(circle, var(--leaf-green) 0%, #8ccf45 55%, var(--white) 72%);
  }
  .city {
    position: absolute; left: 0; width: 1200px; top: 470px; text-align: center;
    font-family: "Kaushan Script", cursive; font-size: 104px; line-height: 1; color: var(--yellow);
  }
  .title {
    position: absolute; left: 0; width: 1200px; top: 570px; text-align: center;
    font-family: "Oswald", sans-serif; font-weight: 700; font-size: 214px; line-height: 1;
    letter-spacing: -4px; color: var(--white);
  }
  .section-head { position: absolute; left: 237px; font-family: "Kaushan Script", cursive; font-size: 178px; line-height: 1; color: var(--yellow); }
  .unit { position: absolute; left: 832px; font-family: "Ubuntu", sans-serif; font-size: 62px; line-height: 1; color: var(--cream); }
  .row { position: absolute; left: 257px; width: 697px; display: flex; justify-content: space-between; font-family: "Ubuntu", sans-serif; font-size: 66px; line-height: 1; }
  .row .name { color: var(--cream); }
  .row .price { color: var(--yellow); }
  .rules { position: absolute; inset: 0; }
  .no-smoking { position: absolute; left: 346px; top: 2655px; width: 104px; height: 104px; }
  .notice { position: absolute; left: 471px; top: 2684px; font-family: "Ubuntu", sans-serif; font-size: 51px; line-height: 1; color: var(--cream); }
</style>
</head>
<body>
<main class="menu-card">
  <div class="backdrop" role="img" aria-label="Low-poly faceted background in brown, copper and dark wine tones"></div>

  <svg class="frame" width="1200" height="2878" viewBox="0 0 1200 2878">
    <path d="M43 189 Q600 -110 1172 189 L1172 2686 Q600 2990 43 2686 Z" fill="none" stroke="#ece6cc" stroke-width="4"/>
  </svg>

  <div class="emblem"><div class="emblem-fill" role="img" aria-label="Green cannabis leaf illustration"></div></div>

  <div class="city">Amsterdam</div>
  <h1 class="title">MENU</h1>

  <h2 class="section-head" style="top:832px">Weed</h2>
  <div class="unit" style="top:913px">p/g</div>
  <div class="row" style="top:1055px"><span class="name">Oblivane</span><span class="price">€16</span></div>
  <div class="row" style="top:1181px"><span class="name">Cloudplum</span><span class="price">€14</span></div>
  <div class="row" style="top:1308px"><span class="name">Tide Runner</span><span class="price">€14</span></div>
  <div class="row" style="top:1435px"><span class="name">Quincefig</span><span class="price">€16</span></div>
  <div class="row" style="top:1561px"><span class="name">Mega Marsh</span><span class="price">€14</span></div>
  <div class="row" style="top:1688px"><span class="name">Grey Heron</span><span class="price">€14</span></div>

  <h2 class="section-head" style="top:1860px">Hash</h2>
  <div class="unit" style="top:1962px">p/g</div>
  <div class="row" style="top:2110px"><span class="name">Tashar Amber</span><span class="price">€12</span></div>
  <div class="row" style="top:2236px"><span class="name">Pebble Frost</span><span class="price">€11</span></div>
  <div class="row" style="top:2363px"><span class="name">Lime Dunes</span><span class="price">€14</span></div>
  <div class="row" style="top:2489px"><span class="name">Ash Petal</span><span class="price">€10</span></div>

  <svg class="rules" width="1200" height="2878" viewBox="0 0 1200 2878" fill="#ece6cc" stroke="#ece6cc" stroke-width="3">
    <g>
      <line x1="240" y1="1143" x2="974" y2="1143"/><circle cx="242" cy="1143" r="4"/><circle cx="972" cy="1143" r="4"/>
      <line x1="240" y1="1269" x2="974" y2="1269"/><circle cx="242" cy="1269" r="4"/><circle cx="972" cy="1269" r="4"/>
      <line x1="240" y1="1395" x2="974" y2="1395"/><circle cx="242" cy="1395" r="4"/><circle cx="972" cy="1395" r="4"/>
      <line x1="240" y1="1521" x2="974" y2="1521"/><circle cx="242" cy="1521" r="4"/><circle cx="972" cy="1521" r="4"/>
      <line x1="240" y1="1648" x2="974" y2="1648"/><circle cx="242" cy="1648" r="4"/><circle cx="972" cy="1648" r="4"/>
      <line x1="240" y1="1774" x2="974" y2="1774"/><circle cx="242" cy="1774" r="4"/><circle cx="972" cy="1774" r="4"/>
      <line x1="240" y1="2189" x2="974" y2="2189"/><circle cx="242" cy="2189" r="4"/><circle cx="972" cy="2189" r="4"/>
      <line x1="240" y1="2316" x2="974" y2="2316"/><circle cx="242" cy="2316" r="4"/><circle cx="972" cy="2316" r="4"/>
      <line x1="240" y1="2443" x2="974" y2="2443"/><circle cx="242" cy="2443" r="4"/><circle cx="972" cy="2443" r="4"/>
      <line x1="240" y1="2569" x2="974" y2="2569"/><circle cx="242" cy="2569" r="4"/><circle cx="972" cy="2569" r="4"/>
    </g>
  </svg>

  <svg class="no-smoking" viewBox="0 0 104 104" role="img" aria-label="No smoking">
    <rect x="24" y="56" width="54" height="10" fill="#ffffff"/>
    <rect x="72" y="56" width="6" height="10" fill="#e0262b"/>
    <path d="M30 50 q-6 -10 2 -18 q6 -6 0 -14" fill="none" stroke="#ffffff" stroke-width="3"/>
    <path d="M38 50 q-6 -10 2 -18" fill="none" stroke="#ffffff" stroke-width="3"/>
    <circle cx="52" cy="52" r="44" fill="none" stroke="#e0262b" stroke-width="9"/>
    <line x1="21" y1="21" x2="83" y2="83" stroke="#e0262b" stroke-width="9"/>
  </svg>
  <p class="notice">NO CIGARETTES</p>
</main>
</body>
</html>
```